New Business Card Design

We would like to refresh our business cards and make them look better. We are an IT company specialising in Cloud Services, IT Managed Services, software and hardware. I have attached a PSD of our current design. Also attached our logo.
Updates

I have uploaded all new logos in EPS format.

Can you please edit all designs to include a job title for Marcus Hollis, eg. General Manager

Industry/Entity Type

Software

Colors
ffffff

Requirements
Must have
• Please use white background.
Should not have
• Black background

```html
<!DOCTYPE html>
<html lang="en">
<head>
<meta charset="utf-8">
<title>Meridian Systems – Business Cards</title>
<link rel="stylesheet" href="https://fonts.googleapis.com/css2?family=Source+Sans+3:wght@400;700&display=swap">
<style>
  :root {
    --bg: #e6e6ea;
    --card: #ffffff;
    --slate: #7e8b98;
    --red: #c0392b;
    --ink: #1f2328;
    --text: #2e3136;
    --white: #ffffff;
  }
  * { margin: 0; padding: 0; box-sizing: border-box; }
  html, body { width: 1200px; height: 987px; overflow: hidden; }
  body {
    background: var(--bg);
    font-family: "Source Sans 3", "Myriad Pro", Arial, sans-serif;
    position: relative;
  }
  .card {
    position: absolute;
    width: 600px;
    height: 360px;
    background: var(--card);
    border-radius: 28px;
    overflow: hidden;
    box-shadow: 0 10px 28px rgba(0,0,0,0.14);
  }
  .card--back { left: 540px; top: 70px; }
  .card--front { left: 60px; top: 540px; }

  .wordmark {
    display: flex;
    align-items: center;
    gap: 12px;
    color: var(--ink);
    font-weight: 400;
    letter-spacing: 0.12em;
    white-space: nowrap;
  }
  .wordmark__dot {
    flex: none;
    border-radius: 50%;
    background: var(--red);
  }

  /* Back card */
  .card--back .wordmark {
    position: absolute;
    left: 70px;
    top: 84px;
    font-size: 44px;
  }
  .card--back .wordmark__dot { width: 28px; height: 28px; }
  .tagline {
    position: absolute;
    left: 70px;
    top: 190px;
    width: 470px;
    font-size: 22px;
    line-height: 1.35;
    color: var(--text);
  }

  /* Front card */
  .front-art { position: absolute; inset: 0; }
  .card--front .wordmark {
    position: absolute;
    left: 36px;
    top: 146px;
    font-size: 26px;
  }
  .card--front .wordmark__dot { width: 20px; height: 20px; }
  .contact {
    position: absolute;
    left: 36px;
    top: 210px;
    list-style: none;
    font-size: 17px;
    line-height: 1.55;
    color: var(--text);
  }
  .contact li { display: flex; align-items: center; gap: 8px; }
  .contact svg { width: 14px; height: 14px; flex: none; }
  .person {
    position: absolute;
    right: 36px;
    top: 112px;
    text-align: right;
    color: var(--white);
  }
  .person__name { font-size: 26px; font-weight: 700; }
  .person__title { font-size: 19px; font-weight: 400; }
</style>
</head>
<body>

  <section class="card card--back" aria-label="Card back">
    <div class="wordmark"><span class="wordmark__dot"></span>Meridian Systems</div>
    <p class="tagline">We are an IT company specializing in Cloud Services, IT Managed Services, software and hardware</p>
  </section>

  <section class="card card--front" aria-label="Card front">
    <svg class="front-art" viewBox="0 0 600 360" aria-hidden="true">
      <path d="M40 0 C 222 10, 352 90, 422 200 S 502 330, 522 360 L 600 360 L 600 0 Z" fill="var(--slate)"/>
      <path d="M18 0 C 200 10, 330 90, 400 200 S 480 330, 500 360" fill="none" stroke="var(--red)" stroke-width="9"/>
    </svg>

    <div class="wordmark"><span class="wordmark__dot"></span>Meridian Systems</div>

    <ul class="contact">
      <li>
        <svg viewBox="0 0 14 14"><circle cx="7" cy="7" r="7" fill="var(--red)"/><path d="M4.5 3.5 L6 3.5 L6.5 5.5 L5.6 6.2 Q6.5 8 7.8 8.6 L8.6 7.7 L10.5 8.3 L10.5 9.8 Q7 10.5 4.5 7 Q3.8 5 4.5 3.5 Z" fill="var(--white)"/></svg>
        07 3000 4815
      </li>
      <li>
        <svg viewBox="0 0 14 14"><circle cx="7" cy="7" r="7" fill="var(--red)"/><rect x="5" y="3" width="4" height="8" rx="0.8" fill="var(--white)"/></svg>
        0400 555 217
      </li>
      <li>
        <svg viewBox="0 0 14 14"><circle cx="7" cy="7" r="7" fill="var(--red)"/><rect x="3.5" y="4.5" width="7" height="5" fill="var(--white)"/><path d="M3.5 4.5 L7 7.5 L10.5 4.5" fill="none" stroke="var(--red)" stroke-width="0.8"/></svg>
        marcus@meridianit.com.au
      </li>
      <li>
        <svg viewBox="0 0 14 14"><circle cx="7" cy="7" r="7" fill="var(--red)"/><circle cx="7" cy="7" r="3.6" fill="none" stroke="var(--white)" stroke-width="0.9"/><path d="M3.4 7 H10.6 M7 3.4 V10.6" stroke="var(--white)" stroke-width="0.9"/></svg>
        www.meridianit.com.au
      </li>
    </ul>

    <div class="person">
      <p class="person__name">Marcus Hollis</p>
      <p class="person__title">General Manager</p>
    </div>
  </section>

</body>
</html>
```